RWT Fittings Ltd Business Cards

We need a business card with our business logo. We provide window and door installations on high-rises in west coast British Colombia, Canada.

I would like my business information and details on one side of the card, and the other side the company name with logo

Target Market(s)

General Contractors

Industry/Entity Type

Construction

Contact Information for Business Card

one side i want my company name and logo in the dark theme logo that i provided

Requirements
Must have
• Marco Peltieri, 16045518293, RWTFittings@mailbox-demo.com, 1407-5194 Linden Row Burnaby BC, V5H 2K9, Owner & Manager

```html
<!DOCTYPE html>
<html lang="en">
<head>
<meta charset="utf-8">
<title>RWT Fittings Ltd – Business Cards</title>
<link rel="stylesheet" href="https://fonts.googleapis.com/css2?family=Open+Sans:wght@400;600;700&display=swap">
<style>
  :root {
    --backdrop: #2a2a2b;
    --card: #1f1f23;
    --accent: #29abe2;
    --white: #ffffff;
    --grey: #a6a6a8;
    --emboss: #3a3a3f;
    --rule: #9a9a9e;
  }
  * { box-sizing: border-box; margin: 0; padding: 0; }
  html, body {
    width: 1200px; height: 780px; overflow: hidden;
    background: var(--backdrop);
    font-family: "Open Sans", Arial, sans-serif;
  }
  .sheet {
    width: 1200px; height: 780px;
    display: flex; align-items: center; justify-content: center; gap: 60px;
  }
  .card {
    position: relative;
    width: 525px; height: 300px;
    background: var(--card);
    border-radius: 20px;
    border-left: 8px solid var(--accent);
    box-shadow: 0 12px 30px rgba(0,0,0,.55);
    overflow: hidden;
  }
  /* front side */
  .front .brand {
    position: absolute; inset: 0;
    display: flex; align-items: center; justify-content: center; gap: 16px;
  }
  .brand-mark { width: 34px; height: 34px; background: var(--accent); }
  .front .brand-name {
    font-weight: 700; font-size: 40px; letter-spacing: 1px;
    color: var(--emboss);
  }
  /* back side */
  .back .brand {
    position: absolute; left: 40px; top: 130px;
    display: flex; align-items: center; gap: 10px;
  }
  .back .brand-mark { width: 22px; height: 22px; }
  .back .brand-name {
    font-weight: 700; font-size: 24px; color: var(--accent);
  }
  .divider {
    position: absolute; left: 272px; top: 40px;
    width: 1px; height: 150px; background: var(--rule);
  }
  .contact {
    position: absolute; left: 294px; top: 42px; right: 16px;
    color: var(--white);
  }
  .person-name { font-weight: 700; font-size: 25px; line-height: 1.1; }
  .person-name .first { color: var(--accent); }
  .person-name .last { color: var(--grey); }
  .person-role { font-weight: 600; font-size: 13px; margin-top: 3px; }
  .details { list-style: none; margin-top: 18px; }
  .details li {
    display: flex; align-items: center; gap: 8px;
    font-size: 11.5px; line-height: 1.85; white-space: nowrap;
  }
  .details svg { width: 12px; height: 12px; flex: none; fill: var(--accent); }
  .address {
    position: absolute; left: 0; right: 0; bottom: 30px;
    text-align: center; color: var(--white); font-size: 14px;
  }
</style>
</head>
<body>
<main class="sheet">
  <section class="card front" aria-label="Card front">
    <div class="brand">
      <span class="brand-mark"></span>
      <span class="brand-name">RWT Fittings Ltd</span>
    </div>
  </section>

  <section class="card back" aria-label="Card back">
    <div class="brand">
      <span class="brand-mark"></span>
      <span class="brand-name">RWT Fittings Ltd</span>
    </div>
    <span class="divider"></span>
    <div class="contact">
      <p class="person-name"><span class="first">Marco</span> <span class="last">Peltieri</span></p>
      <p class="person-role">Managing Director</p>
      <ul class="details">
        <li>
          <svg viewBox="0 0 24 24" aria-hidden="true"><path d="M6.6 10.8a15.1 15.1 0 0 0 6.6 6.6l2.2-2.2a1 1 0 0 1 1-.25 11.4 11.4 0 0 0 3.6.57 1 1 0 0 1 1 1V20a1 1 0 0 1-1 1A17 17 0 0 1 3 4a1 1 0 0 1 1-1h3.5a1 1 0 0 1 1 1c0 1.25.2 2.45.57 3.57a1 1 0 0 1-.25 1z"/></svg>
          (604) 551-8293
        </li>
        <li>
          <svg viewBox="0 0 24 24" aria-hidden="true"><path d="M3 5h18a1 1 0 0 1 1 1v12a1 1 0 0 1-1 1H3a1 1 0 0 1-1-1V6a1 1 0 0 1 1-1zm9 7.5L4 7.5V9l8 5 8-5V7.5z"/></svg>
          RWTFittings@mailbox-demo.com
        </li>
        <li>
          <svg viewBox="0 0 24 24" aria-hidden="true"><path d="M12 2a10 10 0 1 0 0 20 10 10 0 0 0 0-20zm6.9 6h-3a15.6 15.6 0 0 0-1.3-3.9A8 8 0 0 1 18.9 8zM12 4c.8 1.2 1.5 2.5 1.9 4h-3.8c.4-1.5 1.1-2.8 1.9-4zM4.3 14a8 8 0 0 1 0-4h3.4a16 16 0 0 0 0 4zm.8 2h3a15.6 15.6 0 0 0 1.3 3.9A8 8 0 0 1 5.1 16zm3-8h-3a8 8 0 0 1 4.3-3.9C8.8 5.3 8.4 6.6 8.1 8zM12 20c-.8-1.2-1.5-2.5-1.9-4h3.8c-.4 1.5-1.1 2.8-1.9 4zm2.3-6H9.7a14.6 14.6 0 0 1 0-4h4.6a14.6 14.6 0 0 1 0 4zm.3 5.9c.6-1.2 1-2.5 1.3-3.9h3a8 8 0 0 1-4.3 3.9zM16.3 14a16 16 0 0 0 0-4h3.4a8 8 0 0 1 0 4z"/></svg>
          www.rwtfittings-demo.com
        </li>
      </ul>
    </div>
    <p class="address">1407-5194 Linden Row Burnaby BC, V5H 2K9</p>
  </section>
</main>
</body>
</html>
```